New Bicycle shop business card

Hi!
I'm looking for a business card for my new proffesional bike mechanics shop. This shop is only for fixing broken bikes and not selling bikes.
Peferbly a modern and sleek and modern design.
Colors: black, grey, red, white
Information:
Name: Rijwielwerkplaats Vanhoutte
Shop owner: Bart Vanhoutte & Marieke Segers
Website: www.rijwielwerkplaats-vanhoutte.be
Email: info@rijwielwerkplaats-vanhoutte.be
Phone number: +32471902368
Street adres: Kerkweg 46
9940 Bellebeke
Slogan/shop information: Herstellingen van alle merken.
Logo: see files.
Target Market(s)
People who seek a mechanic to fix or upgrade their bikes.
Contact Information for Business Card
Information:
Website: info@rijwielwerkplaats-vanhoutte.be
9940 Bellebeke
Logo: see files.

```html
<!DOCTYPE html>
<html lang="nl">
<head>
<meta charset="utf-8">
<title>Rijwielwerkplaats Vanhoutte – visitekaartje</title>
<link rel="stylesheet" href="https://fonts.googleapis.com/css2?family=Roboto:wght@400;500;700&display=swap">
<style>
  :root {
    --stage: #3b3b3d;
    --card: #231d1c;
    --red: #d8323f;
    --grey: #d9d9d9;
    --text: #ececec;
    --muted: #cfcfcf;
  }
  * { margin: 0; padding: 0; box-sizing: border-box; }
  html, body { width: 1200px; height: 901px; overflow: hidden; }
  body {
    background: var(--stage);
    font-family: "Roboto", sans-serif;
    display: flex;
    flex-direction: column;
    align-items: center;
    justify-content: center;
    gap: 54px;
  }
  .card {
    position: relative;
    width: 640px;
    height: 366px;
    background: var(--card);
    overflow: hidden;
    box-shadow: 0 14px 30px rgba(0,0,0,.35);
  }
  .brand {
    display: flex;
    align-items: center;
    gap: 12px;
  }
  .brand-dot {
    width: 30px; height: 30px;
    border-radius: 50%;
    background: var(--red);
    flex: none;
  }
  .brand-name {
    color: var(--text);
    font-weight: 700;
    font-size: 20px;
    line-height: 1.15;
    letter-spacing: .5px;
    text-transform: uppercase;
  }
  /* back side */
  .card-back .brand {
    position: absolute;
    left: 50%; top: 50%;
    transform: translate(-50%, -50%);
    width: 300px;
  }
  .card-back .brand-name { font-size: 24px; }
  /* front side */
  .card-front .brand {
    position: absolute;
    left: 40px; top: 78px;
    width: 230px;
  }
  .details {
    position: absolute;
    left: 300px; top: 92px;
    right: 24px;
    color: var(--muted);
    font-size: 13px;
    line-height: 1.55;
  }
  .details-title {
    color: var(--red);
    font-size: 20px;
    font-weight: 500;
    line-height: 1.2;
    margin-bottom: 2px;
  }
  .details-owner { margin-bottom: 8px; }
  .details-address { margin-bottom: 8px; }
  .contact-list { list-style: none; }
  .contact-list li { display: flex; align-items: center; gap: 8px; }
  .contact-list svg { width: 12px; height: 12px; flex: none; }
  .footer-strip {
    position: absolute;
    left: 0; bottom: 0;
    width: 100%; height: 30px;
  }
  .slogan {
    position: absolute;
    right: 22px; bottom: 7px;
    color: #fff;
    font-size: 13px;
  }
</style>
</head>
<body>

<section class="card card-back" aria-label="Achterkant visitekaartje">
  <div class="brand">
    <span class="brand-dot"></span>
    <span class="brand-name">Rijwielwerkplaats Vanhoutte</span>
  </div>
</section>

<section class="card card-front" aria-label="Voorkant visitekaartje">
  <div class="brand">
    <span class="brand-dot"></span>
    <span class="brand-name">Rijwielwerkplaats Vanhoutte</span>
  </div>

  <div class="details">
    <h1 class="details-title">Rijwielwerkplaats Vanhoutte</h1>
    <p class="details-owner">Shop owner: Bart Vanhoutte &amp; Marieke Segers</p>
    <p class="details-address">Kerkweg 46<br>9940 Bellebeke</p>
    <ul class="contact-list">
      <li>
        <svg viewBox="0 0 24 24" aria-hidden="true"><path fill="var(--red)" d="M6.6 10.8a15.1 15.1 0 0 0 6.6 6.6l2.2-2.2a1 1 0 0 1 1-.25 11.4 11.4 0 0 0 3.6.57 1 1 0 0 1 1 1V20a1 1 0 0 1-1 1A17 17 0 0 1 3 4a1 1 0 0 1 1-1h3.5a1 1 0 0 1 1 1c0 1.25.2 2.45.57 3.57a1 1 0 0 1-.25 1z"/></svg>
        +32471902368
      </li>
      <li>
        <svg viewBox="0 0 24 24" aria-hidden="true"><path fill="var(--red)" d="M2 5h20v14H2z"/><path d="M2 5l10 8 10-8" fill="none" stroke="var(--card)" stroke-width="2"/></svg>
        info@rijwielwerkplaats-vanhoutte.be
      </li>
      <li>
        <svg viewBox="0 0 24 24" aria-hidden="true"><circle cx="12" cy="12" r="10" fill="var(--red)"/><path d="M2 12h20M12 2c3 3 3 17 0 20M12 2c-3 3-3 17 0 20" fill="none" stroke="var(--card)" stroke-width="1.5"/></svg>
        www.rijwielwerkplaats-vanhoutte.be
      </li>
    </ul>
  </div>

  <svg class="footer-strip" viewBox="0 0 640 30" preserveAspectRatio="none" aria-hidden="true">
    <rect x="0" y="18" width="640" height="12" fill="var(--grey)"/>
    <polygon points="300,30 330,0 640,0 640,30" fill="var(--red)"/>
  </svg>
  <p class="slogan">Herstellingen van alle merken.</p>
</section>

</body>
</html>
```